Landscaping flier 2024

Create a 1 page flier for landscaping services
1. Must be completed in Adobe Photoshop
2. Size 8.5" x 11" (portrait layout)
3. Include logo
4. Text to include:
2024 Gravesite Landscaping Packages
info@hollowbrookmemorial.org
(201) 555-0148
hollowbrookmemorial.org
5. Use chart text for the content. DO NOT COPY THE CHART DESIGN/FORMAT. Use the chart for the text you need only.
6. Use "Pricing cards as format for laying out the chart". Open to other ideas as well.
**Use the example of chart design (handwritten) to base your design off of.
7. Photos
-include before and after care photos

```html
<!DOCTYPE html>
<html lang="en">
<head>
<meta charset="utf-8">
<title>Hollowbrook Memorial – 2024 Gravesite Landscaping Packages</title>
<link href="https://fonts.googleapis.com/css2?family=Poppins:wght@400;500;600;700;800&display=swap" rel="stylesheet">
<style>
:root{
  --wine:#7b1e2c;
  --wine-dark:#5a1019;
  --wine-deep:#3e0a10;
  --ink:#1f1f1f;
  --tab-dark:#232323;
  --gold:#d6b60a;
  --card:#f3f3f3;
  --row:#e7e7e7;
  --band:#d9d9d9;
  --text:#333;
  --muted:#555;
  --tick:#3fae3a;
  --cross:#e2363d;
  --stage:#ececec;
  --white:#fff;
}
*{box-sizing:border-box;margin:0;padding:0}
html,body{width:1200px;height:2366px;overflow:hidden}
body{
  background:var(--stage);
  font-family:"Poppins",sans-serif;
  color:var(--text);
  display:flex;align-items:center;justify-content:center;
}
.flier{
  position:relative;width:913px;height:1182px;background:var(--white);
  transform:scale(1.2);transform-origin:center;
  box-shadow:0 6px 24px rgba(0,0,0,.18);
  overflow:hidden;
}
/* brand */
.brand{
  position:absolute;top:70px;left:0;right:0;
  display:flex;align-items:center;justify-content:center;gap:22px;
  font-weight:600;font-size:38px;letter-spacing:1px;color:var(--wine);
  text-transform:uppercase;
}
.brand-dot{width:78px;height:78px;border-radius:50%;border:2px solid var(--wine);flex:none}
/* hero band */
.hero{position:absolute;top:164px;left:0;width:913px;height:370px}
.hero-bg{position:absolute;inset:0;width:100%;height:100%}
.title{position:absolute;top:194px;left:0;right:0;text-align:center;color:var(--white);text-transform:uppercase}
.title-main{display:block;font-weight:800;font-size:74px;line-height:1;letter-spacing:.5px}
.title-sub{display:block;font-weight:700;font-size:44px;line-height:1.1;margin-top:2px}
.shot{position:absolute;top:181px;width:397px}
.shot-before{left:47px}
.shot-after{left:468px}
.shot-photo{height:191px;background:linear-gradient(180deg,#7c8a6a 0%,#5d9a2e 25%,#6fb437 60%,#5e9c2c 100%);border:2px solid var(--white);border-bottom:0}
.shot-after .shot-photo{background:linear-gradient(180deg,#6f7d5e 0%,#4f8a2a 30%,#71b83b 65%,#63a030 100%)}
.shot-label{height:36px;background:var(--wine);color:var(--white);font-weight:700;font-size:26px;text-align:center;line-height:38px;text-transform:uppercase}
/* footer */
.footer{position:absolute;left:0;bottom:0;width:913px;height:163px;background:var(--wine)}
.valid{position:absolute;top:1092px;left:0;right:0;text-align:center;color:var(--white);font-weight:700;font-size:17px;text-transform:uppercase}
.contacts{position:absolute;top:1116px;left:0;right:0;display:flex;justify-content:center;align-items:center;gap:14px;color:var(--white);font-weight:500;font-size:18.5px}
.contact{display:flex;align-items:center;gap:10px}
.contact svg{width:32px;height:32px;flex:none}
/* cards */
.plans{position:absolute;top:599px;left:47px;display:flex;gap:7px}
.card{position:relative;width:268px;height:480px;background:var(--card);border-radius:0 0 14px 14px;box-shadow:0 2px 6px rgba(0,0,0,.12)}
.card-band{position:relative;z-index:1;height:108px;background:var(--band);clip-path:polygon(0 0,100% 0,100% 72%,50% 100%,0 72%);padding-top:68px;text-align:center;font-weight:600;font-size:9.5px;line-height:1.25;color:#2a2a2a;text-transform:uppercase}
.card-tab{position:absolute;z-index:3;top:-9px;left:31px;width:206px;height:72px;background:var(--wine);clip-path:polygon(0 0,100% 0,100% 62%,50% 100%,0 62%);color:var(--white);text-align:center;font-weight:700;font-size:13.5px;line-height:1.3;padding-top:12px;text-transform:uppercase}
.card-tab.dark{background:var(--tab-dark)}
.card-tab.featured{padding-top:5px;height:68px}
.popular{display:block;width:100%;background:var(--gold);color:var(--wine-dark);font-size:10.5px;font-weight:500;line-height:15px;margin-top:2px}
.lead{text-align:center;padding:7px 10px 8px}
.feature{display:flex;align-items:flex-start;gap:7px;font-size:14px;line-height:1.15;color:var(--text)}
.lead .feature{justify-content:center;text-align:center}
.note{font-size:9.5px;line-height:1.2;color:var(--muted);margin-top:7px}
.rows .feature{padding:7px 10px 7px 30px;min-height:34px;align-items:center}
.rows .feature:nth-child(odd){background:var(--row)}
.icon{width:14px;height:14px;flex:none;margin-top:1px}
.price{text-align:center;padding-top:16px;font-size:11.5px;color:var(--text)}
.price-pill{display:inline-block;background:var(--wine);color:var(--white);font-weight:700;font-size:27px;line-height:32px;border-radius:5px;padding:0 26px;margin:4px 0 5px}
.price-pill sup,.term-pill sup{font-size:.5em;vertical-align:top;position:relative;top:2px}
.terms{display:flex;justify-content:center;gap:22px;margin-bottom:8px}
.term{font-weight:700;font-size:10px;text-transform:uppercase;color:#2a2a2a}
.term-pill{display:block;margin-top:3px;background:var(--wine);color:var(--white);font-size:12px;border-radius:4px;padding:1px 9px}
.price-note{font-size:12px;line-height:1.2}
</style>
</head>
<body>
<main class="flier">
  <header class="brand">
    <span>Hollowbrook</span><span class="brand-dot"></span><span>Memorial</span>
  </header>

  <section class="hero">
    <svg class="hero-bg" viewBox="0 0 913 370" preserveAspectRatio="none" role="img" aria-label="Autumn trees in deep red tones behind the heading">
      <defs>
        <linearGradient id="foliage" x1="0" y1="0" x2="1" y2="1">
          <stop offset="0" stop-color="#4a0c14"/>
          <stop offset=".45" stop-color="#7b1e2c"/>
          <stop offset="1" stop-color="#521018"/>
        </linearGradient>
      </defs>
      <path d="M0 25 H368 C388 5 420 0 455 0 C490 0 522 5 543 25 H913 V370 H0 Z" fill="url(#foliage)"/>
    </svg>
    <div class="shot shot-before">
      <div class="shot-photo" role="img" aria-label="Overgrown gravesite before landscaping"></div>
      <div class="shot-label">Before</div>
    </div>
    <div class="shot shot-after">
      <div class="shot-photo" role="img" aria-label="Neatly trimmed boxwood bed at gravesite after landscaping"></div>
      <div class="shot-label">After</div>
    </div>
  </section>

  <h1 class="title">
    <span class="title-main">2024 Gravesite</span>
    <span class="title-sub">Landscaping Packages</span>
  </h1>

  <footer class="footer"></footer>

  <section class="plans">
    <article class="card">
      <div class="card-tab">Seasonal<br>Care</div>
      <div class="card-band">Seasonal<br>Landscaping Care</div>
      <div class="lead">
        <div class="feature"><svg class="icon" viewBox="0 0 14 14"><circle cx="7" cy="7" r="7" fill="var(--tick)"/><path d="M3.8 7.2l2.2 2.2 4.2-4.4" stroke="#fff" stroke-width="1.8" fill="none"/></svg><span>Weeding &amp; trimming on<br>your gravesite</span></div>
        <p class="note">Approximately every 7 weeks during the growing<br>season : mid-April through mid-October</p>
      </div>
      <div class="rows">
        <div class="feature"><svg class="icon" viewBox="0 0 14 14"><circle cx="7" cy="7" r="7" fill="var(--cross)"/><path d="M4.5 4.5l5 5M9.5 4.5l-5 5" stroke="#fff" stroke-width="1.7"/></svg>Monument leveling</div>
        <div class="feature"><svg class="icon" viewBox="0 0 14 14"><circle cx="7" cy="7" r="7" fill="var(--cross)"/><path d="M4.5 4.5l5 5M9.5 4.5l-5 5" stroke="#fff" stroke-width="1.7"/></svg><span>Payment ensures grave<br>care forever</span></div>
        <div class="feature"><svg class="icon" viewBox="0 0 14 14"><circle cx="7" cy="7" r="7" fill="var(--cross)"/><path d="M4.5 4.5l5 5M9.5 4.5l-5 5" stroke="#fff" stroke-width="1.7"/></svg>Full bed of boxwood shrubs</div>
        <div class="feature"><svg class="icon" viewBox="0 0 14 14"><circle cx="7" cy="7" r="7" fill="var(--cross)"/><path d="M4.5 4.5l5 5M9.5 4.5l-5 5" stroke="#fff" stroke-width="1.7"/></svg>Replacement of shrubs</div>
        <div class="feature"><svg class="icon" viewBox="0 0 14 14"><circle cx="7" cy="7" r="7" fill="var(--cross)"/><path d="M4.5 4.5l5 5M9.5 4.5l-5 5" stroke="#fff" stroke-width="1.7"/></svg>Trust certificate</div>
      </div>
      <div class="price">
        <div class="terms">
          <div class="term">3 Years<span class="term-pill"><sup>$</sup>396</span></div>
          <div class="term">2 Years<span class="term-pill"><sup>$</sup>264</span></div>
          <div class="term">1 Years<span class="term-pill"><sup>$</sup>132</span></div>
        </div>
        <p class="price-note">Multi-year payment locks in<br>current rates</p>
      </div>
    </article>

    <article class="card">
      <div class="card-tab dark">Basic Care<br>Endowment</div>
      <div class="card-band">Landscaping care forever<br>with no plasting</div>
      <div class="lead">
        <div class="feature"><svg class="icon" viewBox="0 0 14 14"><circle cx="7" cy="7" r="7" fill="var(--tick)"/><path d="M3.8 7.2l2.2 2.2 4.2-4.4" stroke="#fff" stroke-width="1.8" fill="none"/></svg><span>Weeding &amp; trimming on<br>your gravesite</span></div>
        <p class="note">2 times per year : mid-May &amp;<br>mid-September</p>
      </div>
      <div class="rows">
        <div class="feature"><svg class="icon" viewBox="0 0 14 14"><circle cx="7" cy="7" r="7" fill="var(--tick)"/><path d="M3.8 7.2l2.2 2.2 4.2-4.4" stroke="#fff" stroke-width="1.8" fill="none"/></svg>Monument leveling</div>
        <div class="feature"><svg class="icon" viewBox="0 0 14 14"><circle cx="7" cy="7" r="7" fill="var(--tick)"/><path d="M3.8 7.2l2.2 2.2 4.2-4.4" stroke="#fff" stroke-width="1.8" fill="none"/></svg><span>Payment ensures grave<br>care forever</span></div>
        <div class="feature"><svg class="icon" viewBox="0 0 14 14"><circle cx="7" cy="7" r="7" fill="var(--cross)"/><path d="M4.5 4.5l5 5M9.5 4.5l-5 5" stroke="#fff" stroke-width="1.7"/></svg>Full bed of boxwood shrubs</div>
        <div class="feature"><svg class="icon" viewBox="0 0 14 14"><circle cx="7" cy="7" r="7" fill="var(--cross)"/><path d="M4.5 4.5l5 5M9.5 4.5l-5 5" stroke="#fff" stroke-width="1.7"/></svg>Replacement of shrubs</div>
        <div class="feature"><svg class="icon" viewBox="0 0 14 14"><circle cx="7" cy="7" r="7" fill="var(--cross)"/><path d="M4.5 4.5l5 5M9.5 4.5l-5 5" stroke="#fff" stroke-width="1.7"/></svg>Trust certificate</div>
      </div>
      <div class="price">
        <p>12 monthly payments of</p>
        <span class="price-pill"><sup>$</sup>287</span>
        <p class="price-note">Call for single payment discount</p>
      </div>
    </article>

    <article class="card">
      <div class="card-tab featured">Perpetual Care<br>Endowment<span class="popular">MOST POPULAR</span></div>
      <div class="card-band">Landscaping care forever<br>for graves with plastry</div>
      <div class="lead">
        <div class="feature"><svg class="icon" viewBox="0 0 14 14"><circle cx="7" cy="7" r="7" fill="var(--tick)"/><path d="M3.8 7.2l2.2 2.2 4.2-4.4" stroke="#fff" stroke-width="1.8" fill="none"/></svg><span>Weeding &amp; trimming on<br>your gravesite</span></div>
        <p class="note">Approximately every 7 weeks during the growing<br>season : mid-April through mid-October</p>
      </div>
      <div class="rows">
        <div class="feature"><svg class="icon" viewBox="0 0 14 14"><circle cx="7" cy="7" r="7" fill="var(--tick)"/><path d="M3.8 7.2l2.2 2.2 4.2-4.4" stroke="#fff" stroke-width="1.8" fill="none"/></svg>Monument leveling</div>
        <div class="feature"><svg class="icon" viewBox="0 0 14 14"><circle cx="7" cy="7" r="7" fill="var(--tick)"/><path d="M3.8 7.2l2.2 2.2 4.2-4.4" stroke="#fff" stroke-width="1.8" fill="none"/></svg><span>Payment ensures grave<br>care forever</span></div>
        <div class="feature"><svg class="icon" viewBox="0 0 14 14"><circle cx="7" cy="7" r="7" fill="var(--tick)"/><path d="M3.8 7.2l2.2 2.2 4.2-4.4" stroke="#fff" stroke-width="1.8" fill="none"/></svg>Full bed of boxwood shrubs</div>
        <div class="feature"><svg class="icon" viewBox="0 0 14 14"><circle cx="7" cy="7" r="7" fill="var(--tick)"/><path d="M3.8 7.2l2.2 2.2 4.2-4.4" stroke="#fff" stroke-width="1.8" fill="none"/></svg>Replacement of shrubs</div>
        <div class="feature"><svg class="icon" viewBox="0 0 14 14"><circle cx="7" cy="7" r="7" fill="var(--tick)"/><path d="M3.8 7.2l2.2 2.2 4.2-4.4" stroke="#fff" stroke-width="1.8" fill="none"/></svg>Trust certificate</div>
      </div>
      <div class="price">
        <p>12 monthly payments of</p>
        <span class="price-pill"><sup>$</sup>351</span>
        <p class="price-note">Call for single payment discount</p>
      </div>
    </article>
  </section>

  <p class="valid">Valid through 10/31/2024</p>
  <div class="contacts">
    <span class="contact">
      <svg viewBox="0 0 32 32"><circle cx="16" cy="16" r="14.5" fill="var(--ink)" stroke="#fff" stroke-width="2"/><path d="M11 9.5c1-.8 2-.6 2.5.3l1.3 2.4c.4.8.1 1.6-.6 2l-.8.5c.8 1.8 2.1 3.2 3.9 4l.5-.8c.5-.7 1.3-.9 2-.5l2.4 1.3c.9.5 1 1.6.3 2.5-1.3 1.6-3 1.9-5 1-3.6-1.6-6.2-4.3-7.6-7.9-.7-1.9-.3-3.6 1.1-4.8z" fill="#fff"/></svg>
      (201) 555-0148
    </span>
    <span class="contact">
      <svg viewBox="0 0 32 32"><circle cx="16" cy="16" r="14.5" fill="var(--ink)" stroke="#fff" stroke-width="2"/><rect x="9" y="11" width="14" height="10" rx="1.5" fill="#fff"/><path d="M9.5 11.5l6.5 5 6.5-5" stroke="var(--ink)" stroke-width="1.4" fill="none"/></svg>
      info@hollowbrookmemorial.org
    </span>
    <span class="contact">
      <svg viewBox="0 0 32 32"><circle cx="16" cy="16" r="14.5" fill="var(--ink)" stroke="#fff" stroke-width="2"/><g stroke="#fff" stroke-width="1.4" fill="none"><circle cx="16" cy="16" r="7.5"/><ellipse cx="16" cy="16" rx="3.2" ry="7.5"/><path d="M8.5 16h15M9.5 12.5h13M9.5 19.5h13"/></g></svg>
      www.hollowbrookmemorial.org
    </span>
  </div>
</main>
</body>
</html>
```